Delivery Docket urgent plus require many other designs for more stationary after this.

We need a new delivery docket design urgently as the one we have needs updating and we have changed our company name. Please do not copy the one I have uploaded as we do not feel this looks professional enough. I uploaded it as a few designers requested to see what we are currently using thank you.
It is quite complex in that we need a range of information to be on the one docket.
We are a Transport Company based in Australia that has a wide variety of items that we deliver such as water, sand and gravels and heavy equipment transport.
We would prefer to keep this design to A5 size as we will get them made into books. We are looking for a modern professional look. Although it is only a delivery docket this is given to all our customers so needs to look impressive.

We need our new logo on the docket (WTR). There will also need to be areas for our address and contact numbers, email etc these will be supplied to the winning designer to make the final adjustments so for now just put something generic in these spaces.
Needs to have an area for customer details, purchase order number, date and docket number (docket number to be in red)
Needs a section where we can list the type of product / and or service that has been provided and the amount / qty usually 3 lines will be enough for this. Need area under this where the customer can sign name and print name to say that the goods / and or services have been received.

Also required somewhere on the docket are the words, Tax Invoice will be issued based on the information provided on this docket. Conditions on back of page

We then need a separate section on the same page which we will use internally that the staff member can tear off and hand into the office. On this section it needs to have area where the driver can list km at start of job and at end with space to calculate km travelled, details of fuel purchased eg amount and litres, vehicle that is being used. also need to log down wheel bearing temps.
prime mover needs spaces as follows
Steer axel FL____________ Steer axel FR _________ 1st drive axel L_______
1st drive axel R_________ 2nd drive axel L_______ 2nd drive axel R________

For the trailers need something similar x 2 as have 2 trailers
1st axel DS_________ 1st axel PS_________ 2nd axel DS__________
2nd axel PS_________ 3rd axel DS_________ 3rd axel PS__________

I have included a few examples of designs we have used in past and ones that we like so you can get an idea of the colours we prefer, I have included some of the designs we are currently receiving for our logo that I like so you can get idea again of colours we prefer. There is much more we need designed also such as time sheets, more delivery dockets and letter heads so there is a lot of more work available to the winning designer.

Thank you

Customers

Serif
Sans Serif

Designer to choose colors to be used in the design.

• Please don't copy old docket as we do not like it and nned new info on new design thank you

```html
<!DOCTYPE html>
<html lang="en">
<head>
<meta charset="utf-8">
<title>WTR Delivery Docket</title>
<link rel="stylesheet" href="https://fonts.googleapis.com/css2?family=Raleway:wght@500;600;700;800&display=swap">
<style>
  :root {
    --ink: #3a3d4a;
    --panel: #3b3f4d;
    --subpanel: #4d5565;
    --blue: #1ea7f5;
    --blue-light: #9fdcfb;
    --blue-soft: #cfeafb;
    --cell: #eff0f2;
    --grid: #c9d7e6;
    --rule: #b4bcc8;
    --red: #e3151a;
    --white: #ffffff;
    --silver: #c9ccd2;
  }
  * { box-sizing: border-box; margin: 0; padding: 0; }
  html, body { width: 1200px; height: 849px; overflow: hidden; background: var(--white); }
  body { font-family: "Raleway", Arial, sans-serif; color: var(--ink); }
  .docket { position: relative; width: 1200px; height: 849px; overflow: hidden; background: var(--white); }
  .abs { position: absolute; }

  .corner-wash { left: 180px; top: 660px; width: 1020px; height: 189px; background: linear-gradient(170deg, rgba(255,255,255,0) 30%, var(--blue-soft) 60%, var(--blue) 100%); z-index: 0; }

  .title-bar { left: 544px; top: 40px; width: 632px; height: 33px; background: linear-gradient(90deg, var(--blue-light), var(--blue) 55%); display: flex; align-items: center; justify-content: space-between; padding: 0 18px 0 15px; }
  .title-bar .label { font-size: 19px; font-weight: 600; color: var(--ink); }
  .title-bar .docket-title { font-size: 20px; font-weight: 700; color: var(--white); }
  .docket-number { color: var(--red); }

  .header-panel { left: 40px; top: 74px; width: 1136px; height: 118px; background: var(--panel); }
  .brand { position: absolute; left: 28px; top: 14px; font-size: 60px; font-weight: 800; color: var(--silver); letter-spacing: 2px; line-height: 1; }
  .company-contact { position: absolute; left: 30px; top: 82px; width: 460px; font-size: 12px; font-weight: 500; line-height: 15px; color: var(--silver); }
  .field { height: 30px; border: 1px solid #d7dbe3; border-top: none; font-size: 13px; font-weight: 600; color: var(--white); padding: 8px 4px 0; }
  .customer-fields { position: absolute; left: 504px; top: 0; width: 357px; }
  .customer-fields .field:first-child, .date-field .field { border-top: 1px solid #d7dbe3; }
  .date-field { position: absolute; left: 875px; top: 14px; width: 246px; }

  .items { left: 40px; top: 204px; width: 1136px; }
  .items .row { display: grid; grid-template-columns: 181px 655px 300px; }
  .items .head { height: 31px; background: linear-gradient(90deg, var(--blue-light), var(--blue) 30%); color: var(--white); font-size: 20px; font-weight: 700; }
  .items .head div { display: flex; align-items: center; justify-content: center; }
  .items .line div { height: 59px; background: var(--cell); border: 1px solid var(--grid); border-top: none; }
  .items .total { height: 44px; background: var(--panel); color: var(--white); font-size: 20px; font-weight: 800; padding: 10px 0 0 849px; letter-spacing: 0.5px; }

  .tax-note { left: 44px; top: 467px; font-size: 14px; font-weight: 500; line-height: 18px; }
  .sign-line { top: 492px; border-top: 2px solid #8a8e98; }
  .sign-line span { display: block; font-size: 19px; font-weight: 600; text-align: center; padding-top: 9px; }
  .print-name { left: 600px; width: 250px; }
  .signature { left: 890px; width: 282px; }

  .trip-log { left: 36px; top: 532px; width: 1136px; display: grid; grid-template-columns: 161px 191px 196px 187px 192px 209px; border: 1px solid var(--grid); z-index: 1; background: var(--white); }
  .trip-log .th { height: 30px; background: var(--blue); color: var(--white); font-size: 19px; font-weight: 700; display: flex; align-items: center; justify-content: center; }
  .trip-log .td { height: 61px; border-right: 1px solid var(--grid); }
  .trip-log .td:last-child { border-right: none; }

  .bearings { left: 38px; top: 637px; width: 1135px; height: 185px; border: 1px solid var(--rule); z-index: 1; }
  .bearings .head { height: 30px; background: var(--panel); color: var(--white); font-size: 18px; font-weight: 600; text-align: center; padding-top: 5px; }
  .bearings .subhead { display: grid; grid-template-columns: 561px 574px; height: 27px; background: var(--subpanel); color: var(--white); font-size: 18px; font-weight: 600; }
  .bearings .subhead div { text-align: center; padding-top: 3px; }
  .bearings .body { display: grid; grid-template-columns: 561px 287px 287px; height: 126px; background: rgba(236, 238, 242, 0.6); }
  .col { padding: 10px 12px 0; }
  .col + .col { border-left: 1px solid var(--rule); }
  .col-title { font-size: 13px; font-weight: 700; margin-bottom: 4px; }
  .prime { display: grid; grid-template-columns: 1fr 1fr; row-gap: 17px; column-gap: 16px; padding-top: 14px; }
  .trailer { display: grid; grid-template-columns: 1fr 1fr; row-gap: 12px; column-gap: 10px; align-content: start; }
  .trailer .col-title { grid-column: 1 / -1; margin-bottom: 0; }
  .temp { display: flex; align-items: flex-end; gap: 6px; font-size: 16px; font-weight: 600; white-space: nowrap; }
  .trailer .temp { font-size: 14px; }
  .temp::after { content: ""; flex: 1; border-bottom: 1.5px solid var(--ink); margin-bottom: 3px; }
</style>
</head>
<body>
<main class="docket">
  <div class="abs corner-wash" role="img" aria-label="Soft blue decorative wave in the lower corner"></div>

  <div class="abs title-bar">
    <span class="label">Customer Details</span>
    <span class="docket-title">Delivery Docket <span class="docket-number">2050</span></span>
  </div>

  <section class="abs header-panel">
    <div class="brand">WTR</div>
    <p class="company-contact">00 Example Street, Sampletown QLD 0000<br>Ph 00 0000 0000 · info@wtrtransport.example</p>
    <div class="customer-fields">
      <div class="field">Name:</div>
      <div class="field">Order no:</div>
      <div class="field">Contact:</div>
      <div class="field">Billing Address:</div>
    </div>
    <div class="date-field"><div class="field">Date:</div></div>
  </section>

  <section class="abs items">
    <div class="row head"><div>Qty</div><div>Description</div><div>Price</div></div>
    <div class="row line"><div></div><div></div><div></div></div>
    <div class="row line"><div></div><div></div><div></div></div>
    <div class="row line"><div></div><div></div><div></div></div>
    <div class="total">TOTAL</div>
  </section>

  <p class="abs tax-note">Tax Invoice which will be issued based on the information<br>provided on this docket as well as the conditions on back of page.</p>

  <div class="abs sign-line print-name"><span>Print Name</span></div>
  <div class="abs sign-line signature"><span>Customer Signature</span></div>

  <section class="abs trip-log">
    <div class="th">KM/start</div><div class="th">KM/end</div><div class="th">Distance</div>
    <div class="th">Fuel/price</div><div class="th">Fuel/ltrs</div><div class="th">Vehicle Type</div>
    <div class="td"></div><div class="td"></div><div class="td"></div>
    <div class="td"></div><div class="td"></div><div class="td"></div>
  </section>

  <section class="abs bearings">
    <div class="head">Wheel Bearing Temps</div>
    <div class="subhead"><div>Prime Movers</div><div>Trailers</div></div>
    <div class="body">
      <div class="col prime">
        <span class="temp">Steer Axel FL</span><span class="temp">Steer Axel FR</span>
        <span class="temp">1st Drive Axel L</span><span class="temp">1st Drive Axel R</span>
        <span class="temp">2nd Drive Axel L</span><span class="temp">2nd Drive Axel R</span>
      </div>
      <div class="col trailer">
        <span class="col-title">Trailer 1</span>
        <span class="temp">1st Axel DS</span><span class="temp">1st Axel PS</span>
        <span class="temp">2nd Axel DS</span><span class="temp">2nd Axel PS</span>
        <span class="temp">3rd Axel DS</span><span class="temp">3rd Axel PS</span>
      </div>
      <div class="col trailer">
        <span class="col-title">Trailer 2</span>
        <span class="temp">1st Axel DS</span><span class="temp">1st Axel PS</span>
        <span class="temp">2nd Axel DS</span><span class="temp">2nd Axel PS</span>
        <span class="temp">3rd Axel DS</span><span class="temp">3rd Axel PS</span>
      </div>
    </div>
  </section>
</main>
</body>
</html>
```